Belvascotravel.com web design project + logo design

Hi,

We are a Russian online tour operator - sunkettle.com

We are looking to tranmsfer our domain to belvascotravel.com. The website and logo need to be belvascoesque - we are not looking to change our functionality, but we need to make the website much more attracitve to clients, much more wild looking but at the same time remaining a professional travel company.

The main concept of the website should be innovative travel (as belvasco was an innovator). Alternatively, you could go down the artist route and go down the draw / design your own tour road.

On our website the customer is able to combine travel services (hotels, flights, Visa services, and soon chauffeur, car rental etc...) put it into their basket (the basket definitely has to look better than it is at the moment) and pay for it in one go by card.

We are also stressin our customer support with web chat, call centre etc... (call centre number at the top of the page)

We aim to provide an easy user experience, but we need to make it have some more style, so I will be waiting for what you guys can come up with.
Let me know if you have any questions - skype is: mrdolbarin

Industry/Entity Type

It Company

Requirements
Must have
• It is quite a simple task - to take the existing website sunkettle.com and belvascosize it to create belvascotravel.com, the functionality of the website will remain the same and there are not many pages in the website. Homepage, Checkout step1, Checkout step 2 (you can view both of these if you select a service) and the generic pages for T&C''s, Privacy policy etc...

IMPORTANT UPDATE

We are also looking at how the search results will look in the designs, (please do a search on our website for hotel / flight)

```html
<!DOCTYPE html>
<html lang="en">
<head>
<meta charset="utf-8">
<title>Belvasco Travel</title>
<link rel="stylesheet" href="https://fonts.googleapis.com/css2?family=Source+Sans+3:wght@400;600;700&family=Noto+Serif:ital,wght@1,700&display=swap">
<style>
:root{
  --orange:#f39a12;
  --orange-dark:#e0820a;
  --orange-text:#e2870e;
  --blue:#2a8ee6;
  --blue-link:#1a7fd8;
  --ink:#333;
  --muted:#555;
  --line:#d6d6d6;
  --panel-frame:#cfcfcf;
  --card-dark:#3a3a3a;
  --footer:#ececec;
  --footer-bottom:#f4f4f4;
  --white:#fff;
}
*{box-sizing:border-box;margin:0;padding:0}
html,body{width:960px;height:1200px;overflow:hidden}
body{position:relative;background:var(--white);font-family:"Source Sans 3",Arial,sans-serif;color:var(--ink);font-size:11px}
.abs{position:absolute}

/* hero */
.hero{left:0;top:0;width:960px;height:640px;
  background:linear-gradient(180deg,#2c8fe3 0%,#5fb2ee 14%,#2a9fd8 22%,#34b4d6 32%,#6cc8d6 40%,#c9d8d2 50%,#e6dccd 62%,#efe9e0 72%,#fff 100%)}
.hero-fade{left:0;top:420px;width:960px;height:220px;background:linear-gradient(180deg,rgba(255,255,255,0),#fff)}
.headline{left:106px;top:208px;font-family:"Noto Serif",Georgia,serif;font-style:italic;font-weight:700;font-size:29px;line-height:35px;letter-spacing:1.5px;color:var(--white);text-shadow:0 2px 4px rgba(0,0,0,.35)}
.slider-dots{left:784px;top:361px;display:flex;gap:5px}
.slider-dots span{width:14px;height:14px;border-radius:50%;background:#8a8a8a}
.slider-dots span:first-child{background:#333}

/* header */
.top-links{right:104px;top:16px;display:flex;align-items:center;gap:6px;font-size:10px;color:var(--white);letter-spacing:.3px}
.top-links .sep{opacity:.8}
.flag{width:20px;height:12px;background:#2c4d9a;border:1px solid #fff;display:inline-block}
.phone{right:104px;top:46px;font-size:13px;color:var(--white)}
.phone b{color:#1b2a45;font-weight:700}
.nav{left:0;top:77px;width:960px;height:41px;background:linear-gradient(180deg,#fbae2a,#f08c0a);box-shadow:0 2px 3px rgba(0,0,0,.2)}
.nav ul{position:absolute;left:306px;top:0;list-style:none;display:flex;height:41px;align-items:center}
.nav li{font-size:11.5px;font-weight:600;color:var(--white);margin-right:26px;letter-spacing:.3px}
.nav li.active{color:#5a3a10}
.logo{left:104px;top:0;width:176px;height:102px}
.logo-text{left:104px;top:18px;width:176px;text-align:center;font-size:25px;line-height:27px;font-weight:700;color:#2b2b2b}

/* search */
.search-frame{left:104px;top:492px;width:752px;height:256px;background:var(--panel-frame);border-radius:5px}
.search-inner{left:112px;top:500px;width:736px;height:240px;background:var(--white)}
.tab{top:518px;height:29px;background:#f0f0f0;border:1px solid var(--line);border-bottom:none;border-radius:6px 6px 0 0;font-size:11px;font-weight:600;color:#333;text-align:center;line-height:29px}
.tab.active{background:#f7f7f7;color:var(--blue-link)}
.form-box{left:128px;top:546px;width:704px;height:184px;background:linear-gradient(180deg,#f1f1f1,#fafafa);border:1px solid var(--line);border-radius:0 6px 6px 6px}
.lbl{font-size:11px;color:#444}
.field{height:27px;background:var(--white);border:1px solid #ccc;border-radius:3px}
.field.select::after{content:"";position:absolute;right:8px;top:11px;border:5px solid transparent;border-top:5px solid #999}
.placeholder{font-size:9px;color:#999;padding:8px 0 0 12px}
.check{width:15px;height:15px;border:1px solid #bbb;border-radius:3px;background:linear-gradient(#fff,#e8e8e8)}
.q{width:12px;height:12px;border-radius:50%;background:#999;color:#fff;font-size:9px;font-weight:700;text-align:center;line-height:12px}
.btn-search{left:640px;top:689px;width:132px;height:27px;background:linear-gradient(180deg,#fbad2a,#ee8a08);border:1px solid #d9790a;border-radius:2px;color:#fff;font-size:12px;font-weight:600;text-align:center;line-height:25px;letter-spacing:.3px}

/* spotlight */
.spot{left:104px;top:760px;width:497px;height:256px;border:1px solid var(--line);border-radius:5px;background:#fff;overflow:hidden}
.spot-head{left:0;top:0;width:497px;height:28px;background:linear-gradient(180deg,#46a3f0,#2384dc);color:#fff;font-size:12.5px;font-weight:600;padding:5px 0 0 11px}
.spot-pager{right:10px;top:10px;display:flex;gap:5px}
.spot-pager span{width:8px;height:8px;background:#8cc6f6}
.spot-pager span:first-child{background:#fff}
.dest-photo{top:42px;width:144px;height:89px;border:1px solid #ddd}
.dest-title{top:144px;width:150px;font-size:12px;line-height:14.5px;font-weight:600;color:var(--orange-text)}
.dest-text{top:176px;width:150px;font-size:10.5px;line-height:16px;color:#444}
.btn-details{top:215px;width:112px;height:28px;background:#555;border-radius:2px;color:#fff;font-size:11px;font-weight:600;line-height:28px;text-align:center}

/* service cards */
.card{left:615px;width:241px;height:82px;background:linear-gradient(180deg,#4a4a4a,#2e2e2e);border-radius:3px}
.card-icon{left:10px;top:4px;width:76px;height:74px;border-radius:5px;color:#fff;font-weight:700;text-align:center}
.card-icon .word{position:absolute;left:0;bottom:5px;width:100%}
.card-icon svg{position:absolute;left:50%;top:10px;transform:translateX(-50%)}
.ic-visa{background:linear-gradient(180deg,#fdc94a,#f39a12);font-size:17px}
.ic-air{background:linear-gradient(180deg,#a56be6,#7a36c9);font-size:10.5px}
.ic-hotel{background:linear-gradient(180deg,#4fd24a,#169a1c);font-size:17px}
.card-title{left:94px;top:8px;font-size:15px;color:#fff;font-weight:600;letter-spacing:.3px}
.card-text{left:94px;top:27px;width:130px;font-size:10.5px;line-height:16px;color:#eee}
.card-more{right:11px;top:61px;font-size:10.5px;color:#3a9cf0;font-weight:600}

/* footer */
.footer{left:0;top:1032px;width:960px;height:124px;background:var(--footer);border-bottom:1px solid #ddd}
.footer-bottom{left:0;top:1156px;width:960px;height:44px;background:var(--footer-bottom)}
.f-col h4{font-size:12px;font-weight:600;color:#444;margin-bottom:6px}
.f-col p{font-size:10px;line-height:20px;color:#666}
.f-col .addr{line-height:16px}
.f-contact{font-size:10.5px;color:var(--blue-link);display:flex;align-items:center;gap:6px;margin-bottom:10px}
.newsletter-input{left:679px;top:1072px;width:177px;height:26px;background:#fff;border:1px solid #ccc;border-radius:3px;font-size:9.5px;color:#888;padding:7px 0 0 10px}
.btn-signup{left:800px;top:1107px;width:56px;height:22px;background:linear-gradient(180deg,#45a8f5,#1d83dc);border-radius:2px;color:#fff;font-size:10px;text-align:center;line-height:22px}
.copy{left:104px;top:1172px;font-size:10px;color:#666}
.copy span{color:var(--orange-text)}
.social{top:1167px;width:22px;height:22px;border-radius:3px}
</style>
</head>
<body>

<div class="abs hero" role="img" aria-label="Tropical beach with a white parasol, coconuts on a small table and two sun loungers by a turquoise sea"></div>
<div class="abs hero-fade"></div>

<div class="abs headline">Aliquam ullamcorper tempor felis,<br>nec condimentum odio<br>aliquet vitae.</div>
<div class="abs slider-dots"><span></span><span></span><span></span><span></span></div>

<nav class="abs nav">
  <ul>
    <li class="active">HOME</li><li>TOUR &amp; PACKAGES</li><li>OUR SERVICES</li><li>NEWS</li><li>ABOUT US</li><li>FOURM</li><li style="margin-right:0">CONTACT US</li>
  </ul>
</nav>

<svg class="abs logo" viewBox="0 0 176 102">
  <path d="M0 0H176V82L88 101L0 82Z" fill="#f4f4f2" stroke="#c9c9c9" stroke-width="1.5"/>
  <path d="M5 0V79L88 96L171 79V0" fill="none" stroke="#d9d9d6" stroke-width="1"/>
</svg>
<div class="abs logo-text">Belvasco<br>Travel</div>

<div class="abs top-links">
  <span>LOG IN</span><span class="sep">|</span><span>REGISTER</span><span class="sep">|</span>
  <svg width="18" height="14" viewBox="0 0 18 14"><path d="M1 1h3l2 8h9l2-6H5" fill="none" stroke="#fff" stroke-width="1.4"/><circle cx="7" cy="12" r="1.4" fill="#fff"/><circle cx="14" cy="12" r="1.4" fill="#fff"/></svg>
  <span>MY BASKET &nbsp;(ITEM 0 )</span>
  <span class="flag"></span><span>EN</span>
  <svg width="10" height="6"><path d="M0 0h10L5 5z" fill="#fff"/></svg>
</div>
<div class="abs phone"><b>Phone:</b> +7 (495) 555-01-42 &nbsp;(Mon-Fri) Hours: 9:00 am - 18:00</div>

<!-- search panel -->
<div class="abs search-frame"></div>
<div class="abs search-inner"></div>
<div class="abs form-box"></div>
<div class="abs tab active" style="left:128px;width:86px">TICKETS</div>
<div class="abs tab" style="left:216px;width:84px">INFO</div>
<div class="abs tab" style="left:302px;width:84px">HOTELS</div>

<div class="abs lbl" style="left:167px;top:569px">When</div>
<div class="abs field" style="left:213px;top:562px;width:250px"></div>
<div class="abs lbl" style="left:477px;top:569px">Where</div>
<div class="abs field" style="left:522px;top:562px;width:250px"></div>

<div class="abs lbl" style="left:168px;top:607px">There</div>
<div class="abs field" style="left:213px;top:600px;width:170px"><div class="placeholder">DD //MM// YY</div></div>
<svg class="abs" style="left:391px;top:601px" width="24" height="24" viewBox="0 0 24 24"><rect x="0.5" y="0.5" width="23" height="23" fill="#fff" stroke="#6a9fd6"/><rect x="0.5" y="0.5" width="23" height="5" fill="#4f8fd3"/><path d="M0 11h24M0 16h24M0 21h24M6 6v18M12 6v18M18 6v18" stroke="#8cb5e0" stroke-width=".8"/></svg>
<div class="abs lbl" style="left:442px;top:607px">Back</div>
<div class="abs field" style="left:471px;top:600px;width:170px"></div>
<div class="abs check" style="left:654px;top:606px"></div>
<div class="abs lbl" style="left:674px;top:607px">Back</div>
<div class="abs check" style="left:709px;top:606px"></div>
<div class="abs lbl" style="left:729px;top:607px">One Way</div>

<div class="abs lbl" style="left:141px;top:646px">Passengers</div>
<div class="abs field select" style="left:213px;top:639px;width:66px"></div>
<svg class="abs" style="left:285px;top:642px" width="10" height="22" viewBox="0 0 10 22"><circle cx="5" cy="2.5" r="2.5" fill="#222"/><path d="M1 6h8v8H7v8H3v-8H1z" fill="#222"/></svg>
<div class="abs q" style="left:308px;top:647px">?</div>
<div class="abs field select" style="left:330px;top:639px;width:66px"></div>
<svg class="abs" style="left:403px;top:645px" width="8" height="17" viewBox="0 0 8 17"><circle cx="4" cy="2" r="2" fill="#222"/><path d="M1 5h6v6H5.5v6h-3v-6H1z" fill="#222"/></svg>
<div class="abs q" style="left:418px;top:647px">?</div>
<div class="abs field select" style="left:442px;top:639px;width:66px"></div>
<svg class="abs" style="left:515px;top:647px" width="9" height="13" viewBox="0 0 9 13"><circle cx="4.5" cy="2" r="2" fill="#222"/><path d="M1 5h7v4H6v4H3V9H1z" fill="#222"/></svg>
<div class="abs q" style="left:532px;top:647px">?</div>
<div class="abs lbl" style="left:602px;top:646px">Class</div>
<div class="abs field select" style="left:640px;top:639px;width:132px"></div>

<div class="abs btn-search">SEARCH NOW</div>

<!-- spotlight -->
<section class="abs spot">
  <div class="abs spot-head">Spotlight Destinations</div>
  <div class="abs spot-pager"><span></span><span></span><span></span><span></span></div>

  <div class="abs dest-photo" style="left:11px;background:linear-gradient(180deg,#4aa3d8 0%,#6a8a5a 40%,#2fb8c0 62%,#e8dcc0 100%)" role="img" aria-label="Long-tail boats moored below limestone cliffs in clear water"></div>
  <div class="abs dest-title" style="left:11px">Nam fermentum purus id aliquet</div>
  <div class="abs dest-text" style="left:11px">Aenean a nibh eget turpis vehicula tempus</div>
  <div class="abs btn-details" style="left:11px">Package Details &gt;&gt;</div>

  <div class="abs dest-photo" style="left:177px;background:linear-gradient(180deg,#8ec3e8 0%,#b9d9ec 45%,#e6eef2 70%,#d7cbb6 100%)" role="img" aria-label="Family running through the surf on a sunny beach"></div>
  <div class="abs dest-title" style="left:177px">Nam fermentum purus id aliquet</div>
  <div class="abs dest-text" style="left:177px">Aenean a nibh eget turpis vehicula tempus</div>
  <div class="abs btn-details" style="left:177px">Package Details &gt;&gt;</div>

  <div class="abs dest-photo" style="left:342px;background:linear-gradient(180deg,#5b9fe0 0%,#4b7a3a 45%,#9bb0a0 70%,#d9cdb3 100%)" role="img" aria-label="Beach resort with palm trees and people relaxing on the sand"></div>
  <div class="abs dest-title" style="left:342px">Nam fermentum purus id aliquet</div>
  <div class="abs dest-text" style="left:342px">Aenean a nibh eget turpis vehicula tempus</div>
  <div class="abs btn-details" style="left:342px">Package Details &gt;&gt;</div>
</section>

<!-- service cards -->
<div class="abs card" style="top:760px">
  <div class="abs card-icon ic-visa">
    <svg width="26" height="30" viewBox="0 0 26 30"><rect x="1" y="1" width="24" height="28" rx="2" fill="#fff"/><rect x="7" y="10" width="12" height="7" fill="#f39a12"/></svg>
    <div class="word">Визы</div>
  </div>
  <div class="abs card-title">INFO</div>
  <div class="abs card-text">Two options apply for a visa..</div>
  <div class="abs card-more">Read More &gt;&gt;</div>
</div>
<div class="abs card" style="top:847px">
  <div class="abs card-icon ic-air">
    <svg width="34" height="34" viewBox="0 0 34 34"><path d="M30 4l-9 9 3 15-3 3-6-11-7 7 1 5-3 2-3-7-7-3 2-3 5 1 7-7L0 10l3-3 15 3 9-9z" fill="#fff" transform="translate(2 1)"/></svg>
    <div class="word">Авиабилеты</div>
  </div>
  <div class="abs card-title">TICKETS</div>
  <div class="abs card-text">Flights from Tours designer.</div>
  <div class="abs card-more">Read More &gt;&gt;</div>
</div>
<div class="abs card" style="top:934px">
  <div class="abs card-icon ic-hotel">
    <svg width="34" height="28" viewBox="0 0 34 28"><path d="M2 11L17 2l15 9" fill="none" stroke="#fff" stroke-width="3"/><path d="M5 12v14M29 12v14M5 21h24M12 18h16v3H12z" stroke="#fff" stroke-width="2.5" fill="#fff"/><circle cx="9" cy="18" r="2.5" fill="#fff"/></svg>
    <div class="word">Отели</div>
  </div>
  <div class="abs card-title">HOTELS</div>
  <div class="abs card-text">Search Hotels by City Builder</div>
  <div class="abs card-more">Read More &gt;&gt;</div>
</div>

<!-- footer -->
<footer class="abs footer"></footer>
<div class="abs f-col" style="left:104px;top:1049px"><h4>Navigation</h4><p>Home<br>About Us<br>Forum<br>Contacts</p></div>
<div class="abs f-col" style="left:215px;top:1049px"><h4>Help</h4><p>Help<br>Term of Use<br>Privacy Policy<br>Cookies</p></div>
<div class="abs f-col" style="left:342px;top:1049px"><h4>Find Us</h4><p class="addr" style="margin-top:-2px">Sunkettle Limited<br>14 Harbour Lane<br>London, E2 4QT<br>UK</p></div>
<div class="abs f-col" style="left:503px;top:1049px"><h4>Contact Us</h4>
  <div class="f-contact"><svg width="14" height="14" viewBox="0 0 14 14"><rect width="14" height="14" rx="2" fill="#f39a12"/><path d="M4 3l2 2-1 1.5c.6 1.3 1.4 2.1 2.5 2.5L9 8l2 2-1.5 1.5C6 11 3 8 2.5 4.5z" fill="#fff"/></svg>+7 (495) 555-01-42</div>
  <div class="f-contact"><svg width="14" height="10" viewBox="0 0 14 10"><rect width="14" height="10" fill="#f39a12"/><path d="M0 0l7 6 7-6" fill="none" stroke="#fff" stroke-width="1.2"/></svg>info@sunkettle.com</div>
</div>
<div class="abs f-col" style="left:679px;top:1049px"><h4>Newsletter SignUp</h4></div>
<div class="abs newsletter-input">Enter Email</div>
<div class="abs btn-signup">SIGN UP</div>

<div class="abs footer-bottom"></div>
<div class="abs copy">Copyright © &nbsp;2013. <span>Belvasco Travel</span>. All Right Reserved</div>
<div class="abs social" style="left:771px;background:#2fa5e0"></div>
<div class="abs social" style="left:801px;background:#3b5e9e"></div>
<div class="abs social" style="left:831px;background:#fff;border:2px solid #4a6a90"></div>

</body>
</html>
```